Vantro cards

I am in the auto motive, transportation business I would like a business card that is Something cool, modern edgy, having to do with car culture. I offer towing service for high and exotic cars. I also provide towing for collisions and car accidents. I offer open and enclosed transport nationwide.

Target Market(s)

Car culture people high end auto collectors

Industry/Entity Type

Towing car carrier

Contact Information for Business Card

My company colors black yellow and silver

Font styles to use
Serif

```html
<!DOCTYPE html>
<html lang="en">
<head>
<meta charset="UTF-8">
<title>Vantro Cards</title>
<link href="https://fonts.googleapis.com/css2?family=Arimo:wght@400;700&display=swap" rel="stylesheet">
<style>
  :root {
    --backdrop: #c9c9c9;
    --card-black: #1c1c1c;
    --card-deep: #151515;
    --accent-yellow: #f7e25b;
    --silver: #c4c4c4;
    --text-white: #ffffff;
    --ink: #1a1a1a;
  }
  * { box-sizing: border-box; margin: 0; padding: 0; }
  html, body {
    width: 1200px; height: 788px; overflow: hidden;
    background: var(--backdrop);
    font-family: "Arimo", Arial, sans-serif;
  }
  .canvas {
    width: 1200px; height: 788px;
    display: flex; align-items: center; justify-content: center; gap: 40px;
  }
  .card {
    position: relative;
    width: 560px; height: 320px;
    background: var(--card-black);
    box-shadow: 0 10px 24px rgba(0,0,0,0.3);
    overflow: hidden;
  }
  /* front */
  .brand-mark {
    position: absolute; top: 62px; left: 250px;
    display: flex; align-items: center; gap: 10px;
  }
  .brand-dot { width: 16px; height: 16px; border-radius: 50%; background: var(--accent-yellow); }
  .brand-name {
    font-weight: 700; font-size: 38px; letter-spacing: 2px;
    color: var(--silver);
  }
  .identity {
    position: absolute; left: 70px; top: 178px; text-align: right; width: 190px;
  }
  .person-name {
    color: var(--accent-yellow); font-weight: 700; font-size: 21px; letter-spacing: 0.5px;
  }
  .person-role { color: var(--text-white); font-size: 14px; margin-top: 2px; }
  .divider {
    position: absolute; left: 280px; top: 150px; width: 1px; height: 92px;
    background: var(--accent-yellow);
  }
  .contact-list {
    position: absolute; left: 300px; top: 148px; list-style: none;
  }
  .contact-list li {
    display: flex; align-items: center; gap: 9px;
    color: var(--text-white); font-size: 13.5px; height: 23px;
  }
  .contact-list svg { width: 12px; height: 12px; flex: none; }
  .address-band {
    position: absolute; left: 0; right: 0; bottom: 24px; height: 30px;
    background: var(--accent-yellow);
    display: flex; align-items: center; padding-left: 170px;
    color: var(--ink); font-size: 13.5px;
  }
  /* back */
  .card--back { background: var(--card-deep); }
  .emblem-pattern {
    position: absolute; inset: 0;
    background: linear-gradient(135deg, #121212 0%, #1e1e1e 55%, #2a2a2a 100%);
  }
  .back-mark {
    position: absolute; top: 50%; left: 50%; transform: translate(-50%, -50%);
    display: flex; align-items: center; gap: 12px;
  }
  .back-mark .brand-name { font-size: 46px; }
</style>
</head>
<body>
<main class="canvas">

  <section class="card card--front">
    <div class="brand-mark">
      <span class="brand-dot"></span>
      <span class="brand-name">VANTRO</span>
    </div>

    <div class="identity">
      <p class="person-name">DORIAN VALE</p>
      <p class="person-role">CEO/Founder</p>
    </div>

    <span class="divider"></span>

    <ul class="contact-list">
      <li>
        <svg viewBox="0 0 12 12"><path fill="#f7e25b" d="M2.5 1l2 2-1 1.3c.6 1.4 1.7 2.5 3.2 3.2L8 6.5l2 2-1.3 1.8C5 10 2 7 1.7 3.2z"/></svg>
        (555) 218 4470
      </li>
      <li>
        <svg viewBox="0 0 12 12"><rect x="3" y="0.8" width="6" height="10.4" rx="1" fill="none" stroke="#f7e25b" stroke-width="1.3"/></svg>
        (555) 903 6125
      </li>
      <li>
        <svg viewBox="0 0 12 12"><rect x="0.8" y="2.5" width="10.4" height="7" fill="#f7e25b"/><path d="M0.8 2.5L6 6.5l5.2-4" fill="none" stroke="#1c1c1c" stroke-width="1"/></svg>
        info@vantrohaul.com
      </li>
      <li>
        <svg viewBox="0 0 12 12"><circle cx="6" cy="6" r="5.2" fill="#f7e25b"/><path d="M0.8 6h10.4M6 0.8v10.4M2 3.3h8M2 8.7h8" stroke="#1c1c1c" stroke-width="0.7" fill="none"/></svg>
        www.vantrohaul.com
      </li>
    </ul>

    <div class="address-band">P.O. Box 3870 Ridgeline Ave Halden AB 6120</div>
  </section>

  <section class="card card--back">
    <div class="emblem-pattern" role="img" aria-label="Faint repeating pattern of the company emblem across a black background"></div>
    <div class="back-mark">
      <span class="brand-dot"></span>
      <span class="brand-name">VANTRO</span>
    </div>
  </section>

</main>
</body>
</html>
```